Business is called "Keel Ledger". Accounting and tax services.

I need a flyer for my new business "Keel Ledger". I am an individual accountant working for himself on the Sunshine Coast in Queensland Australia. I would like to see designs that communicate reliability and trust. I believe my point of difference is that I am always available to my clients and I will cap my number of clients to ensure I can service them properly. Accountants in general seem to have a bad reputation for not responding to clients in a timely fashion, whether by email or phone. This is where I intend to differentiate myself. I have included my business card for ideas on colour and for contact information. I have also included some logo's that should go on the flyer. With the RFN logo, the words "Keel Ledger is a RFN Business" needs to be written either above, below or to the right hand side (as per the business card).

Target Market(s)

Small business owners and individuals requiring taxation and financials

Industry/Entity Type

Public Accounting

Font styles to use
Serif

Requirements
Must have
• Supplied logo's, accounting style pictures etc
Services: Small Business Taxation
Company & Trust Tax Returns
Rental Property Returns
Capital Gains Tax
Individual Tax Returns
BAS and IAS lodgements
Nice to have
• Needs to convey a sense of being reliable and responds to clients quickly.
Should not have
• My name

```html
<!DOCTYPE html>
<html lang="en">
<head>
<meta charset="utf-8">
<title>Keel Ledger – Tax and Accounting Services</title>
<link rel="stylesheet" href="https://fonts.googleapis.com/css2?family=Montserrat:wght@400;500;700;800;900&display=swap">
<style>
  :root {
    --teal: #27a98a;
    --teal-dark: #1f8e73;
    --charcoal: #2f3233;
    --ink: #2b2b2b;
    --muted: #c9c9c9;
    --white: #ffffff;
  }
  * { margin: 0; padding: 0; box-sizing: border-box; }
  html, body { width: 885px; height: 1200px; overflow: hidden; background: #ffffff; }
  .flyer {
    position: relative;
    width: 885px;
    height: 1200px;
    overflow: hidden;
    background: var(--white);
    font-family: "Montserrat", Arial, sans-serif;
    color: var(--ink);
  }
  .flyer-art { position: absolute; inset: 0; }

  .brand {
    position: absolute;
    left: 0; top: 12px;
    width: 414px;
    text-align: center;
  }
  .brand-mark {
    display: block;
    width: 70px; height: 70px;
    margin: 0 auto;
    border: 3px solid var(--charcoal);
    border-radius: 50%;
  }
  .brand-name {
    margin-top: 10px;
    font-size: 25px;
    font-weight: 500;
    letter-spacing: 9px;
    color: var(--charcoal);
  }

  .headline {
    position: absolute;
    left: 60px; top: 360px;
    color: var(--white);
    font-size: 42px;
    line-height: 50px;
    text-transform: uppercase;
  }
  .headline .light { font-weight: 400; }
  .headline .heavy { font-weight: 900; }

  .services-title {
    position: absolute;
    left: 60px; top: 566px;
    font-size: 39px;
    font-weight: 900;
    color: var(--teal);
  }
  .service-list { position: absolute; left: 60px; top: 634px; list-style: none; }
  .service {
    display: flex;
    align-items: center;
    height: 77px;
  }
  .service-icon { width: 54px; height: 54px; flex: none; }
  .service-label {
    margin-left: 20px;
    font-size: 16.5px;
    line-height: 21px;
    font-weight: 500;
    text-transform: uppercase;
    color: var(--ink);
  }

  .badge-label {
    position: absolute;
    font-size: 13.5px;
    font-weight: 800;
    line-height: 15px;
    text-align: center;
    text-transform: uppercase;
    color: var(--ink);
  }
  .badge-label.local { left: 474px; top: 865px; width: 120px; }
  .badge-label.reliable { left: 706px; top: 874px; width: 120px; }

  .partner {
    position: absolute;
    display: flex;
    align-items: center;
    font-size: 17px;
    font-weight: 700;
    color: var(--charcoal);
  }
  .partner-dot {
    width: 22px; height: 22px;
    margin-right: 7px;
    border-radius: 50%;
    background: var(--teal);
  }
  .partner-box {
    width: 22px; height: 22px;
    margin-right: 7px;
    background: var(--charcoal);
  }
  .partner.tallyo { left: 448px; top: 966px; }
  .partner.rfn { left: 580px; top: 966px; }
  .rfn-note {
    position: absolute;
    left: 540px; top: 996px;
    width: 160px;
    font-size: 10px;
    font-weight: 500;
    line-height: 13px;
    text-align: center;
    color: var(--ink);
  }
  .agent-seal {
    position: absolute;
    left: 760px; top: 958px;
    width: 36px; height: 36px;
    border-radius: 50%;
    background: var(--muted);
  }

  .contact {
    position: absolute;
    right: 33px; top: 1072px;
    text-align: right;
    font-style: normal;
    color: var(--white);
  }
  .contact-title {
    font-size: 18px;
    font-weight: 800;
    line-height: 20px;
    text-transform: uppercase;
    margin-bottom: 10px;
  }
  .contact-line {
    display: flex;
    justify-content: flex-end;
    align-items: center;
    font-size: 17px;
    line-height: 22px;
    font-weight: 400;
  }
  .contact-icon { width: 17px; height: 17px; margin-left: 9px; }
</style>
</head>
<body>
<main class="flyer">
  <svg class="flyer-art" width="885" height="1200" viewBox="0 0 885 1200">
    <defs>
      <linearGradient id="office-tone" x1="0" y1="0" x2="0.4" y2="1">
        <stop offset="0" stop-color="#c9b48a"/>
        <stop offset="0.45" stop-color="#8a6f4e"/>
        <stop offset="1" stop-color="#3c3128"/>
      </linearGradient>
      <linearGradient id="cash-tone" x1="0" y1="0" x2="1" y2="1">
        <stop offset="0" stop-color="#5e5a57"/>
        <stop offset="0.5" stop-color="#bdb8ae"/>
        <stop offset="1" stop-color="#ece8e2"/>
      </linearGradient>
      <linearGradient id="signing-tone" x1="0" y1="0" x2="0" y2="1">
        <stop offset="0" stop-color="#5a4a40"/>
        <stop offset="0.4" stop-color="#c9a288"/>
        <stop offset="0.8" stop-color="#efe9e3"/>
        <stop offset="1" stop-color="#ffffff"/>
      </linearGradient>
    </defs>

    <polygon class="photo-office" role="img" aria-label="Photo of an accountant with headphones working at a computer in an office"
             points="0,141 376,141 550,389 406,546 0,546" fill="url(#office-tone)"/>
    <polygon class="photo-cash" role="img" aria-label="Photo of hands counting banknotes above a ledger and pen"
             points="452,0 885,0 885,388 548,392 384,126" fill="url(#cash-tone)"/>
    <polygon class="photo-signing" role="img" aria-label="Photo of hands signing a paper document with a pen"
             points="556,402 885,397 885,735 620,745 418,553" fill="url(#signing-tone)"/>

    <g class="service-strengths">
      <rect x="590" y="824" width="130" height="46" fill="var(--charcoal)"/>
      <rect x="590" y="824" width="48" height="46" fill="var(--teal)"/>
      <path d="M630 830 h46 M630 847 h54 M630 864 h46" stroke="#ffffff" stroke-width="4" stroke-linecap="round"/>
      <circle cx="534" cy="847" r="78" fill="#ffffff" stroke="var(--teal)" stroke-width="13"/>
      <circle cx="766" cy="847" r="78" fill="#ffffff" stroke="var(--charcoal)" stroke-width="13"/>
      <g class="icon-local" fill="var(--teal)">
        <circle cx="528" cy="809" r="11"/>
        <path d="M508 852 q0 -26 20 -26 q20 0 20 26 z"/>
        <circle cx="552" cy="844" r="10" fill="var(--teal-dark)"/>
        <text x="552" y="849" font-size="13" font-weight="700" fill="#ffffff" text-anchor="middle" font-family="Montserrat, sans-serif">$</text>
      </g>
      <g class="icon-reliable" fill="none" stroke="var(--teal)" stroke-width="4" stroke-linecap="round" stroke-linejoin="round">
        <rect x="742" y="808" width="46" height="40" rx="6"/>
        <path d="M753 828 l9 9 l16 -18"/>
      </g>
    </g>

    <polygon class="band-charcoal" points="0,1083 885,1168 885,1200 0,1200" fill="var(--charcoal)"/>
    <polygon class="band-teal" points="285,1200 885,1036 885,1200" fill="var(--teal)"/>
  </svg>

  <header class="brand">
    <span class="brand-mark"></span>
    <p class="brand-name">KEEL LEDGER</p>
  </header>

  <h1 class="headline">
    <span class="heavy">Tax</span> <span class="light">and</span><br>
    <span class="heavy">Accounting</span><br>
    <span class="light">Services</span>
  </h1>

  <h2 class="services-title">SERVICES</h2>
  <ul class="service-list">
    <li class="service">
      <svg class="service-icon" viewBox="0 0 54 54"><circle cx="27" cy="27" r="24" fill="none" stroke="var(--teal)" stroke-width="3"/><rect x="18" y="14" width="18" height="25" rx="2" fill="none" stroke="var(--teal)" stroke-width="2.5"/><path d="M22 22h10M22 27h10M22 32h7" stroke="var(--teal)" stroke-width="2.5"/></svg>
      <span class="service-label">Small<br>Business Taxation</span>
    </li>
    <li class="service">
      <svg class="service-icon" viewBox="0 0 54 54"><circle cx="27" cy="27" r="24" fill="none" stroke="var(--teal)" stroke-width="3"/><rect x="15" y="17" width="24" height="20" rx="2" fill="none" stroke="var(--teal)" stroke-width="2.5"/><text x="27" y="32" font-size="13" font-weight="700" fill="var(--teal)" text-anchor="middle" font-family="Montserrat, sans-serif">$</text></svg>
      <span class="service-label">Company &amp;<br>Trust Tax Returns</span>
    </li>
    <li class="service">
      <svg class="service-icon" viewBox="0 0 54 54"><circle cx="27" cy="27" r="24" fill="none" stroke="var(--teal)" stroke-width="3"/><path d="M16 27 L27 17 L38 27 M19 25 V37 H35 V25" fill="none" stroke="var(--teal)" stroke-width="2.5" stroke-linejoin="round"/></svg>
      <span class="service-label">Rental<br>Property Returns</span>
    </li>
    <li class="service">
      <svg class="service-icon" viewBox="0 0 54 54"><circle cx="27" cy="27" r="24" fill="none" stroke="var(--teal)" stroke-width="3"/><rect x="20" y="14" width="18" height="24" rx="2" fill="none" stroke="var(--teal)" stroke-width="2.5"/><text x="29" y="31" font-size="13" font-weight="700" fill="var(--teal)" text-anchor="middle" font-family="Montserrat, sans-serif">$</text><circle cx="19" cy="35" r="6" fill="var(--teal)"/></svg>
      <span class="service-label">Capital<br>Gains Tax</span>
    </li>
    <li class="service">
      <svg class="service-icon" viewBox="0 0 54 54"><circle cx="27" cy="27" r="24" fill="none" stroke="var(--teal)" stroke-width="3"/><circle cx="27" cy="27" r="13" fill="none" stroke="var(--teal)" stroke-width="2.5" stroke-dasharray="60 8"/><text x="27" y="33" font-size="16" font-weight="700" fill="var(--teal)" text-anchor="middle" font-family="Montserrat, sans-serif">$</text></svg>
      <span class="service-label">Individual<br>Tax Returns</span>
    </li>
    <li class="service">
      <svg class="service-icon" viewBox="0 0 54 54"><circle cx="27" cy="27" r="24" fill="none" stroke="var(--teal)" stroke-width="3"/><path d="M18 14 H32 L37 19 V40 H18 Z" fill="none" stroke="var(--teal)" stroke-width="2.5" stroke-linejoin="round"/><path d="M22 24h11M22 29h11M22 34h11" stroke="var(--teal)" stroke-width="2.5"/></svg>
      <span class="service-label">BAS and<br>IAS Lodgements</span>
    </li>
  </ul>

  <p class="badge-label local">Local<br>Accountant</p>
  <p class="badge-label reliable">Reliable</p>

  <div class="partner tallyo"><span class="partner-dot"></span>Tallyo</div>
  <div class="partner rfn"><span class="partner-box"></span>RFN</div>
  <p class="rfn-note">Keel Ledger is a RFN Business</p>
  <div class="agent-seal"></div>

  <address class="contact">
    <p class="contact-title">Contact<br>Keel Ledger</p>
    <p class="contact-line">0412 580 396
      <svg class="contact-icon" viewBox="0 0 18 18"><circle cx="9" cy="9" r="8" fill="none" stroke="#fff" stroke-width="1.4"/><path d="M6 5 l2 2 l-1 1.5 q1 2 2.5 2.5 l1.5 -1 l2 2 l-1 1.5 q-5 -0.5 -7.5 -6 z" fill="#fff"/></svg>
    </p>
    <p class="contact-line">office@keelledger.com.au
      <svg class="contact-icon" viewBox="0 0 18 18"><circle cx="9" cy="9" r="8" fill="none" stroke="#fff" stroke-width="1.4"/><rect x="5" y="6" width="8" height="6" fill="none" stroke="#fff" stroke-width="1.2"/><path d="M5 6 l4 3.5 l4 -3.5" fill="none" stroke="#fff" stroke-width="1.2"/></svg>
    </p>
    <p class="contact-line">www.keelledger.com.au
      <svg class="contact-icon" viewBox="0 0 18 18"><circle cx="9" cy="9" r="8" fill="none" stroke="#fff" stroke-width="1.4"/><circle cx="9" cy="9" r="5" fill="none" stroke="#fff" stroke-width="1.2"/><path d="M4 9h10M9 4v10" stroke="#fff" stroke-width="1.2"/></svg>
    </p>
  </address>
</main>
</body>
</html>
```